Shine Fox Auto Care Business Card

2 side business card design for an auto detailing business

Target Market(s)

Auto detailing

Contact Information for Business Card

Things included

The business name “Shine Fox Auto Care”
Mark Dunrow
(403)271-6094
Marrow Creek, Sk

Services offered - complete interior& exterior detail
- paint correction & protection
- ceramic coating
- trim restore
- auto carpet & seat cleaning

Requirements
Must have
• Colours that are in my logo

Services offered

My name Mark Dunrow
403-271-6094
Marrow Creek, Sk

Not too sure in what order for these ?
Website. Shinefoxautocare.com
Instagram Shinefoxautocare
Email. Shinefoxautoac@mailvento.com

```html
<!DOCTYPE html>
<html lang="en">
<head>
<meta charset="utf-8">
<title>Shine Fox Auto Care – Business Card</title>
<link href="https://fonts.googleapis.com/css2?family=Arimo:wght@400;700&family=Michroma&display=swap" rel="stylesheet">
<style>
  :root {
    --backdrop: #2b2b2d;
    --card: #1c1d1f;
    --pattern-top: #2a2b2e;
    --pattern-bottom: #1e1f21;
    --red: #a10d0f;
    --white: #f4f4f4;
    --rule: #8a8a8a;
  }
  * { margin: 0; padding: 0; box-sizing: border-box; }
  html, body { width: 1200px; height: 1108px; overflow: hidden; }
  body {
    background: var(--backdrop);
    font-family: "Arimo", Arial, sans-serif;
    color: var(--white);
    position: relative;
  }
  .card {
    position: absolute;
    top: 250px;
    width: 360px;
    height: 600px;
    background: var(--card);
    border-radius: 22px;
    overflow: hidden;
    text-align: center;
  }
  .card--front { left: 200px; }
  .card--back  { left: 640px; }

  /* front */
  .brand {
    position: absolute; top: 120px; left: 0; right: 0;
    display: flex; flex-direction: column; align-items: center; gap: 18px;
  }
  .brand__dot {
    width: 86px; height: 86px; border-radius: 50%;
    border: 9px solid var(--red);
  }
  .brand__name {
    font-family: "Arimo", Arial, sans-serif;
    font-weight: 700; font-size: 30px; letter-spacing: 1px;
    color: var(--white); text-transform: uppercase; line-height: 1.05;
  }
  .person {
    position: absolute; top: 352px; left: 0; right: 0;
    font-family: "Michroma", sans-serif; font-size: 21px;
    color: var(--red); text-transform: uppercase;
  }
  .divider {
    position: absolute; left: 40px; right: 40px;
    display: flex; align-items: center; gap: 8px;
  }
  .divider::before, .divider::after {
    content: ""; flex: 1; height: 1px; background: var(--rule);
  }
  .divider--icons { top: 398px; }
  .divider--place { top: 522px; }
  .icon { width: 26px; height: 26px; }
  .contact {
    position: absolute; top: 436px; left: 0; right: 0;
    font-size: 16px; line-height: 24px;
  }
  .place {
    position: absolute; top: 556px; left: 0; right: 0;
    font-size: 17px;
  }

  /* back */
  .pattern {
    position: absolute; inset: 0 0 auto 0; height: 330px;
    background: linear-gradient(180deg, var(--pattern-top), var(--pattern-bottom));
  }
  .mark {
    position: absolute; top: 205px; left: 0; right: 0;
    display: flex; align-items: center; justify-content: center; gap: 8px;
  }
  .mark__dot { width: 22px; height: 22px; border-radius: 50%; border: 4px solid var(--red); }
  .mark__name { font-weight: 700; font-size: 15px; color: var(--red); text-transform: uppercase; }
  .services { position: absolute; top: 312px; left: 0; right: 0; }
  .services__title {
    display: flex; align-items: center; gap: 10px; margin: 0 30px;
    font-weight: 700; font-size: 19px; letter-spacing: .5px; white-space: nowrap;
  }
  .services__title::before, .services__title::after {
    content: ""; flex: 1; height: 1px; background: var(--white);
  }
  .services__lead { font-size: 13px; text-transform: uppercase; margin-top: 4px; }
  .services__list { list-style: none; margin-top: 8px; font-size: 20px; line-height: 30px; }
  .divider--social { top: 510px; }
  .social-dot { width: 22px; height: 22px; border-radius: 50%; background: var(--white); }
  .handle { position: absolute; top: 546px; left: 0; right: 0; font-size: 17px; }
</style>
</head>
<body>
  <article class="card card--front">
    <div class="brand">
      <span class="brand__dot"></span>
      <span class="brand__name">Shine Fox<br>Auto Care</span>
    </div>
    <p class="person">Mark Dunrow</p>
    <div class="divider divider--icons">
      <svg class="icon" viewBox="0 0 26 26" aria-label="Phone"><circle cx="13" cy="13" r="12" fill="none" stroke="var(--red)" stroke-width="1.5"/><path d="M9 7l3 3-1.5 2a9 9 0 0 0 4 4l2-1.5 3 3-2 2c-5 0-10-5-10-10z" fill="var(--red)"/></svg>
      <svg class="icon" viewBox="0 0 26 26" aria-label="Email"><circle cx="13" cy="13" r="12" fill="none" stroke="var(--red)" stroke-width="1.5"/><rect x="7" y="9" width="12" height="8" fill="var(--red)"/><path d="M7 9l6 5 6-5" fill="none" stroke="var(--card)" stroke-width="1.2"/></svg>
      <svg class="icon" viewBox="0 0 26 26" aria-label="Website"><circle cx="13" cy="13" r="12" fill="none" stroke="var(--red)" stroke-width="1.5"/><circle cx="13" cy="13" r="6" fill="var(--red)"/><path d="M7 13h12M13 7v12" stroke="var(--card)" stroke-width="1"/></svg>
    </div>
    <div class="contact">
      <p>(403)271-6094</p>
      <p>Shinefoxautocare@mailvento.com</p>
      <p>www.Shinefoxautocare.com</p>
    </div>
    <div class="divider divider--place">
      <svg class="icon" viewBox="0 0 26 26" aria-label="Location"><circle cx="13" cy="13" r="12" fill="none" stroke="var(--red)" stroke-width="1.5"/><path d="M13 20s-5-5-5-9a5 5 0 0 1 10 0c0 4-5 9-5 9z" fill="var(--red)"/><circle cx="13" cy="11" r="1.8" fill="var(--card)"/></svg>
    </div>
    <p class="place">Marrow Creek, Sk</p>
  </article>

  <article class="card card--back">
    <div class="pattern" role="img" aria-label="Repeating faint brand pattern"></div>
    <div class="mark"><span class="mark__dot"></span><span class="mark__name">Shine Fox</span></div>
    <section class="services">
      <h2 class="services__title">SERVICES OFFERED</h2>
      <p class="services__lead">Complete interior &amp; exterior detail</p>
      <ul class="services__list">
        <li>Paint correction &amp; protection</li>
        <li>Ceramic coating</li>
        <li>Trim restore</li>
        <li>Auto carpet &amp; seat cleaning</li>
      </ul>
    </section>
    <div class="divider divider--social"><span class="social-dot"></span></div>
    <p class="handle">Shinefoxautocare</p>
  </article>
</body>
</html>
```